Custom unique Stationary design for Logistics company

We need a custom, unique , elegant and luxurious full stationary design using our new logo, following these guidelines:
1- Business card: double sided, both sides uses the navy blue as the background main color (same as the code of the navy blue used in our logo).
2- envelope and folder: also use the same navy blue as the main background color.
3- book cover( notepad cover) : same thing with the navy blue
4- letterhead: feel free to use the combination of the colors in our logo.
5- rest of the items are up to your creativity

Target Market(s)

corporates and other businesses

Industry/Entity Type

Logistics and heavy machines contractors

Requirements
Must have
• Letterhead, business card, envelope, notepad cover, paper, file
Nice to have
• navy blue to be main background color for business card, envelope, notepad cover

```html
<!DOCTYPE html>
<html lang="en">
<head>
<meta charset="utf-8">
<title>Northway Freight Group – Stationery</title>
<link rel="stylesheet" href="https://fonts.googleapis.com/css2?family=Open+Sans:wght@400;600;700&display=swap">
<style>
  :root {
    --navy: #1f5676;
    --orange: #e0603a;
    --paper: #f3f3f3;
    --ground: #e7e7e7;
    --ink: #3a3a3a;
    --white: #ffffff;
  }
  * { margin: 0; padding: 0; box-sizing: border-box; }
  html, body { width: 1200px; height: 795px; overflow: hidden; }
  body {
    background: var(--ground);
    font-family: "Open Sans", Arial, sans-serif;
    color: var(--ink);
    position: relative;
  }
  .sheet { position: absolute; box-shadow: 0 2px 8px rgba(0,0,0,.12); overflow: hidden; }

  .wordmark { font-weight: 700; white-space: nowrap; line-height: 1.1; display: flex; align-items: center; gap: .35em; }
  .wordmark .dot { width: .7em; height: .7em; border-radius: 50%; background: currentColor; display: inline-block; }
  .on-navy { color: var(--white); }
  .on-paper { color: var(--navy); }

  .footer-band { position: absolute; left: 0; right: 0; bottom: 0; }
  .footer-band .stripe { position: absolute; left: 0; bottom: 0; height: 35%; width: 70%; background: var(--orange); }
  .footer-band .tab {
    position: absolute; right: 0; bottom: 0; height: 100%; width: 34%;
    background: var(--navy); color: var(--white); font-weight: 600;
    clip-path: polygon(4% 0, 100% 0, 100% 100%, 0 100%);
    display: flex; align-items: center; justify-content: center;
  }

  /* Letterhead */
  .letterhead { left: 293px; top: 99px; width: 292px; height: 415px; background: var(--paper); }
  .letterhead .header { height: 61px; background: var(--navy); position: relative; }
  .letterhead .header .wordmark { position: absolute; left: 30px; top: 23px; font-size: 12px; }
  .letterhead .contact { position: absolute; left: 190px; top: 11px; font-size: 5.4px; line-height: 7px; color: var(--white); }
  .contact .icon { display: inline-block; width: 4px; height: 4px; background: var(--orange); border-radius: 1px; margin-right: 2px; vertical-align: middle; }
  .letter-body { position: absolute; left: 31px; top: 105px; width: 231px; font-size: 5.1px; line-height: 7.6px; text-align: justify; }
  .letter-body p { margin-bottom: 7.6px; }
  .letterhead .footer-band { height: 11px; font-size: 6px; }
  .letterhead .footer-band .stripe { width: 68%; height: 6px; }

  /* Folder */
  .folder { left: 637px; top: 80px; width: 346px; height: 437px; background: var(--navy); }
  .folder .spine { position: absolute; top: 0; bottom: 0; left: 4px; width: 14px; border-left: 1px solid rgba(0,0,0,.18); border-right: 1px solid rgba(0,0,0,.18); }
  .folder .wordmark { position: absolute; left: 0; right: 0; top: 205px; justify-content: center; font-size: 30px; }
  .folder .tagline { position: absolute; left: 0; right: 0; top: 255px; text-align: center; font-size: 8.5px; font-weight: 700; letter-spacing: .6px; color: #c9d3da; }
  .folder .web { position: absolute; left: 0; right: 0; top: 386px; text-align: center; font-size: 11.5px; color: var(--white); letter-spacing: .3px; }
  .folder .web .accent { color: var(--orange); }

  /* Business cards */
  .card { left: 187px; width: 132px; height: 75px; }
  .card-front { top: 551px; background: var(--navy); }
  .card-front .wordmark { position: absolute; left: 0; right: 0; top: 30px; justify-content: center; font-size: 11px; }
  .card-back { top: 646px; background: var(--paper); }
  .card-back .wordmark { position: absolute; left: 12px; top: 32px; font-size: 7.5px; }
  .card-back .divider { position: absolute; left: 69px; top: 20px; width: 1px; height: 38px; background: var(--navy); }
  .card-back .details { position: absolute; left: 73px; top: 19px; font-size: 3.4px; line-height: 4.6px; }
  .card-back .name { font-size: 5.4px; line-height: 6px; font-weight: 700; color: var(--navy); }
  .card-back .role { color: var(--orange); font-weight: 600; margin-bottom: 3px; }
  .card-back .footer-band { height: 6px; font-size: 3.6px; }
  .card-back .footer-band .stripe { height: 2px; }

  /* Envelope front */
  .envelope-front { left: 353px; top: 561px; width: 329px; height: 157px; background: var(--paper); }
  .envelope-front .wordmark { position: absolute; left: 26px; top: 35px; font-size: 11px; }
  .envelope-front .return { position: absolute; left: 20px; top: 62px; font-size: 5.5px; line-height: 6.4px; text-align: center; width: 74px; }
  .envelope-front .return strong { color: var(--navy); font-weight: 600; }
  .envelope-front .footer-band { height: 12px; font-size: 6.5px; }
  .envelope-front .footer-band .stripe { height: 7px; }

  /* Envelope back */
  .envelope-back { left: 713px; top: 561px; width: 329px; height: 157px; background: var(--paper); }
  .envelope-back .flap {
    position: absolute; left: 0; top: 0; width: 100%; height: 56px; background: var(--navy);
    clip-path: polygon(0 0, 100% 0, 98% 92%, 96% 100%, 4% 100%, 2% 92%);
  }
  .envelope-back .wordmark { position: absolute; left: 0; right: 0; top: 21px; justify-content: center; font-size: 8px; }
</style>
</head>
<body>

<article class="sheet letterhead">
  <header class="header">
    <div class="wordmark on-navy"><span class="dot"></span>Northway</div>
    <address class="contact" style="font-style:normal">
      48 Harbour Crest Road,<br>
      Milton, ON L9T 3K2<br>
      <span style="display:block;height:3px"></span>
      <span class="icon"></span>+15550142233<br>
      <span class="icon"></span>+15550142290<br>
      <span class="icon"></span>hello@northwayfreight.com
    </address>
  </header>
  <div class="letter-body">
    <p>Dear customer,</p>
    <p>Lorem ipsum dolor sit amet, consectetur adipisicing elit, sed do eiusmod tempor incididunt ut labore et dolore magna aliqua. Ut enim ad minim veniam, quis nostrud exercitation ullamco laboris nisi ut aliquip ex ea commodo consequat. Duis aute irure dolor in reprehenderit in voluptate velit esse cillum dolore eu fugiat nulla pariatur. Excepteur sint occaecat cupidatat non proident, sunt in culpa qui officia deserunt mollit anim id est laborum.</p>
    <p>Lorem ipsum dolor sit amet, consectetur adipisicing elit, sed do eiusmod tempor incididunt ut labore et dolore magna aliqua. Ut enim ad minim veniam, quis nostrud exercitation ullamco laboris nisi ut aliquip ex ea commodo consequat. Duis aute irure dolor in reprehenderit in voluptate velit esse cillum dolore eu fugiat nulla pariatur. Excepteur sint occaecat cupidatat non proident, sunt in culpa qui officia deserunt mollit anim id est laborum.</p>
    <p>Lorem ipsum dolor sit amet, consectetur adipisicing elit, sed do eiusmod tempor incididunt ut labore et dolore magna aliqua. Ut enim ad minim veniam, quis nostrud exercitation ullamco laboris nisi ut aliquip ex ea commodo consequat. Duis aute irure dolor in reprehenderit in voluptate velit esse cillum dolore eu fugiat nulla pariatur. Excepteur sint occaecat cupidatat non proident, sunt in culpa qui officia deserunt mollit anim id est laborum.</p>
    <p>Lorem ipsum dolor sit amet, consectetur adipisicing elit, sed do eiusmod tempor incididunt ut labore et dolore magna aliqua. Ut enim ad minim veniam, quis nostrud exercitation ullamco laboris nisi ut aliquip ex ea commodo consequat. Duis aute irure dolor in reprehenderit.</p>
    <p>Yours Sincerely,</p>
  </div>
  <footer class="footer-band">
    <span class="stripe"></span>
    <span class="tab">www.northwayfreight.com</span>
  </footer>
</article>

<article class="sheet folder">
  <span class="spine"></span>
  <div class="wordmark on-navy"><span class="dot"></span>Northway</div>
  <div class="tagline">NORTHWAY FREIGHT GROUP</div>
  <div class="web">www.<span class="accent">northwayfreight</span>.com</div>
</article>

<article class="sheet card card-front">
  <div class="wordmark on-navy"><span class="dot"></span>Northway</div>
</article>

<article class="sheet card card-back">
  <div class="wordmark on-paper"><span class="dot"></span>Northway</div>
  <span class="divider"></span>
  <div class="details">
    <div class="name">Dana R. Ellison</div>
    <div class="role">Managing Director</div>
    1250 Orchard Lane,<br>
    Suite 210 Lakeside.<br>
    (555) 014-7720<br>
    (555) 014-7731<br>
    hello@northwayfreight.com
  </div>
  <footer class="footer-band">
    <span class="stripe"></span>
    <span class="tab">www.northwayfreight.com</span>
  </footer>
</article>

<article class="sheet envelope-front">
  <div class="wordmark on-paper"><span class="dot"></span>Northway</div>
  <address class="return" style="font-style:normal">
    <strong>Northway Freight Group</strong><br>
    48 Harbour Crest Road<br>
    Milton, ON L9T 3K2
  </address>
  <footer class="footer-band">
    <span class="stripe"></span>
    <span class="tab">www.northwayfreight.com</span>
  </footer>
</article>

<article class="sheet envelope-back">
  <div class="flap"></div>
  <div class="wordmark on-navy"><span class="dot"></span>Northway</div>
</article>

</body>
</html>
```